Pellowar

We need logo and wesbsite for a software development company based out of Hyderabad, India focused on startups and mid sized companies focused on build a new software products in USA and Europe countires.

Target Market(s)

startup and midsized companies in teh USA and Europe for software product development.

Industry/Entity Type

software development

Coding

Coded - Design and coding required

Number of Pages Required

5+ page

Requirements
Must have
• latest design concepts and very elegant
Nice to have
• each page should have images that reflects the content
Should not have
• too many colors

```html
<!DOCTYPE html>
<html lang="en">
<head>
<meta charset="utf-8">
<title>Pellowar — Software Product Teams</title>
<link href="https://fonts.googleapis.com/css2?family=Roboto:wght@300;400;500;700;900&display=swap" rel="stylesheet">
<style>
:root{
  --cyan:#1fd3f0;
  --blue:#13a3e8;
  --ink:#1c1c1c;
  --text:#555;
  --dark:#17181b;
  --dark2:#1f2024;
  --white:#fff;
  --line:#d9dde2;
}
*{margin:0;padding:0;box-sizing:border-box}
html,body{width:1200px;height:4205px;overflow:hidden}
body{font-family:'Roboto',sans-serif;color:var(--ink);background:var(--white);position:relative}
section,header,footer{position:absolute;left:0;width:1200px}
.abs{position:absolute}
.btn{position:absolute;display:flex;align-items:center;justify-content:center;font-weight:500;font-size:15px;letter-spacing:.3px;color:var(--white);background:linear-gradient(180deg,var(--cyan),var(--blue));border-radius:3px;text-transform:uppercase}

/* hero */
.hero{top:0;height:790px;background:linear-gradient(110deg,#0d2536 0%,#1a3a4d 35%,#4a4f55 60%,#2a2e33 100%);overflow:hidden}
.brand{position:absolute;left:110px;top:34px;display:flex;align-items:center;gap:12px;color:var(--white);font-size:25px;font-weight:500;letter-spacing:.5px}
.brand-dot{width:36px;height:36px;border-radius:50%;background:var(--cyan)}
.nav{position:absolute;top:43px;left:506px;display:flex;gap:34px;font-size:15.5px;font-weight:500;color:var(--white)}
.nav a{color:inherit;text-decoration:none;padding-bottom:5px}
.nav a.active{border-bottom:2px solid var(--white)}
.hero-title{position:absolute;left:123px;top:232px;font-size:64px;color:var(--white);font-weight:300}
.hero-title b{font-weight:900}
.hero-sub{position:absolute;left:124px;top:312px;width:440px;font-size:22px;line-height:32px;color:var(--white);font-weight:300}
.dots{position:absolute;top:688px;left:557px;display:flex;gap:13px}
.dots i{width:11px;height:11px;border-radius:50%;background:rgba(255,255,255,.45)}
.dots i.on{background:var(--white)}

/* about */
.about{top:790px;height:435px;text-align:center}
.h2{font-size:37px;font-weight:300;text-transform:uppercase}
.h2 b{font-weight:700}
.about .h2{position:absolute;top:66px;width:100%}
.about p{position:absolute;left:145px;width:910px;top:130px;font-size:15px;line-height:29px;color:var(--text)}

/* build */
.build{top:1225px;height:720px;background:linear-gradient(180deg,#1a1b1f,var(--dark2) 50%,#15161a);color:var(--white);text-align:center}
.build .h2{position:absolute;top:94px;width:100%;font-size:38px}
.build p{position:absolute;left:133px;width:934px;top:164px;font-size:14.2px;line-height:29px;color:#dcdcdc}
.card{position:absolute;top:320px;width:307px;height:307px;border:1.5px solid #4a4c52;border-radius:4px;background:rgba(255,255,255,.02)}
.card svg{position:absolute;left:118px;top:38px}
.card h3{position:absolute;top:142px;width:100%;font-size:23px;font-weight:500;text-transform:uppercase}
.card p{position:relative;left:0;width:auto;top:183px;margin:0 18px;font-size:13.6px;line-height:26px;color:#d8d8d8}

/* how */
.how{top:1945px;height:690px}
.how .photo{position:absolute;left:128px;top:86px;width:456px;height:512px;border-radius:8px;background:linear-gradient(140deg,#8c6a52,#b9a999 45%,#4b5866 75%,#2c2f35)}
.how h2{position:absolute;left:634px;top:105px;font-size:37px;line-height:48px;text-transform:uppercase;font-weight:300}
.how h2 b{font-weight:700}
.how ul{position:absolute;left:635px;top:222px;list-style:none}
.how li{font-size:15.5px;color:#333;height:36px;display:flex;align-items:center;gap:12px}
.how li::before{content:"";width:9px;height:9px;border-radius:50%;border:3px solid #7fd9f2;background:var(--blue);box-sizing:content-box;flex:none;transform:scale(.8)}
.how .note{position:absolute;left:637px;top:510px;width:440px;font-size:15.5px;line-height:27px;color:#333}

/* case */
.case{top:2635px;height:555px;background:linear-gradient(180deg,#1aa4e8,#22e2f5);color:var(--white)}
.case .h2{position:absolute;left:117px;top:100px;font-size:38px}
.case p{position:absolute;left:120px;top:168px;width:448px;font-size:13.6px;line-height:30px;text-align:justify}
.case .outline{position:absolute;left:120px;top:397px;width:164px;height:49px;border:2px solid var(--white);border-radius:3px;display:flex;align-items:center;justify-content:center;font-size:16px;font-weight:500}
.case .video{position:absolute;left:620px;top:87px;width:460px;height:384px;background:linear-gradient(150deg,#8a6b57,#c9c4bd 45%,#6f7a86 80%,#3d444c)}
.play{position:absolute;left:205px;top:167px;width:50px;height:50px;border-radius:50%;background:var(--white);display:flex;align-items:center;justify-content:center}

/* contact */
.contact{top:3190px;height:650px}
.contact .h2{position:absolute;left:115px;top:102px;font-size:37px}
.contact .lead{position:absolute;left:116px;top:162px;width:440px;font-size:18px;line-height:31px;color:#666;font-weight:300}
.contact hr{position:absolute;left:110px;top:290px;width:455px;border:0;border-top:1px solid var(--line)}
.info{position:absolute;left:115px;display:flex;align-items:center;gap:16px;font-size:15px;color:#555;line-height:23px}
.info .ic{width:50px;height:50px;border-radius:50%;background:var(--white);box-shadow:0 2px 10px rgba(0,0,0,.12);display:flex;align-items:center;justify-content:center}
.lbl{position:absolute;font-size:15.5px;font-weight:700;color:#222}
.field{position:absolute;border:1px solid var(--line);border-radius:3px;background:var(--white)}

/* footer */
.footer{top:3840px;height:365px;background:var(--dark);color:var(--white)}
.flogo{position:absolute;left:128px;top:60px;width:175px;text-align:center}
.flogo .mark{width:70px;height:70px;border-radius:50%;background:var(--cyan);margin:0 auto 22px}
.flogo span{font-size:26px;font-weight:400;letter-spacing:.5px}
.fcol{position:absolute;top:87px}
.fcol h4{font-size:16px;font-weight:500;margin-bottom:14px;text-transform:uppercase}
.fcol a{display:block;font-size:13px;line-height:26px;color:#ddd;text-decoration:none}
.social{display:flex;gap:9px}
.social i{width:32px;height:32px;border-radius:50%;border:2px solid #bbb;background:#444}
.fcol p{font-size:13px;line-height:26px;color:#ddd;width:250px;margin-top:12px}
.footer hr{position:absolute;left:115px;top:303px;width:978px;border:0;border-top:1px solid #555}
.copy{position:absolute;top:323px;width:100%;text-align:center;font-size:13px;color:#ddd}
</style>
</head>
<body>

<header class="hero">
  <div class="abs" role="img" aria-label="Photo of a team reviewing code and data on a glowing screen" style="inset:0;background:radial-gradient(ellipse at 70% 40%,rgba(210,180,150,.35),transparent 55%),radial-gradient(ellipse at 15% 30%,rgba(60,150,190,.35),transparent 50%)"></div>
  <div class="brand"><span class="brand-dot"></span>PELLOWAR</div>
  <nav class="nav">
    <a class="active">HOME</a><a>ABOUT US</a><a>SERVICES</a><a>TEAM</a><a>CASE STUDY</a><a>CONTACT</a>
  </nav>
  <h1 class="hero-title"><b>PELLO</b>WAR</h1>
  <p class="hero-sub">Teams are the essence of every business. They can create wonders if built with perfection.</p>
  <div class="btn" style="left:124px;top:431px;width:173px;height:50px">Get Started</div>
  <svg class="abs" style="left:66px;top:325px" width="28" height="50"><path d="M22 3 L4 25 L22 47" stroke="#fff" stroke-width="2.5" fill="none"/></svg>
  <svg class="abs" style="left:1106px;top:325px" width="28" height="50"><path d="M6 3 L24 25 L6 47" stroke="#fff" stroke-width="2.5" fill="none"/></svg>
  <div class="dots"><i></i><i class="on"></i><i></i><i></i></div>
  <svg class="abs" style="left:0;top:570px" width="1200" height="220" viewBox="0 0 1200 220">
    <path d="M0 88 Q470 320 1200 18 L1200 220 L0 220 Z" fill="#1fd3f0"/>
    <path d="M0 96 Q470 302 1200 32 L1200 220 L0 220 Z" fill="#fff"/>
  </svg>
</header>

<section class="about">
  <h2 class="h2"><b>About</b> us</h2>
  <p>We are a group of entrepreneurs, technocrats, software architects, and delivery heads who have come together to serve startups, product companies, and enterprises with their product development. We are prompt in understanding your product and help design, build, maintain and operate your product. Pellowar quickly set up a team of UX experts, Business Analysts, Developers and QA resources to build the best team to deliver the product. Businesses can focus on core activities of Sales and Marketing to achieve revenue growth, and we will accelerate in your go-to-market.</p>
  <div class="btn" style="left:513px;top:300px;width:173px;height:50px">Learn More</div>
</section>

<section class="build">
  <h2 class="h2"><b>Build your</b>&nbsp; product</h2>
  <p>As startups are racing to build software as a product, they have stumbling blocks on building software from scratch. One of the reasons is stiff competition. The competition to get the best resources, robust design, and scalable technology is overwhelming. Startup owners must use the CEO mindset while building a software product. Think of the bigger picture. Focus on the outcome and set aside the tiny technical details. Focus on human resources and Process. Software development needs experts. Thus, your team will include:</p>
  <div class="card" style="left:112px">
    <svg width="70" height="70" viewBox="0 0 70 70" fill="none" stroke="#1fc6ee" stroke-width="2"><rect x="4" y="6" width="62" height="42" rx="2"/><path d="M28 48 L26 60 M42 48 L44 60 M20 62 H50"/><path d="M27 22 L20 27 L27 32 M43 22 L50 27 L43 32 M38 18 L32 36"/></svg>
    <h3>Project Manager</h3>
    <p>Lorem ipsum dolor sit amet, consectetur ng elit, sed do eiusmod tempor incididunt ut labore et dolore magna aliqua.</p>
  </div>
  <div class="card" style="left:446px">
    <svg width="70" height="70" viewBox="0 0 70 70" fill="none" stroke="#1fc6ee" stroke-width="2"><circle cx="35" cy="30" r="22"/><circle cx="35" cy="30" r="9"/><path d="M35 2 V8 M35 52 V58 M7 30 H13 M57 30 H63 M12 64 H58"/></svg>
    <h3>Team Lead</h3>
    <p>Lorem ipsum dolor sit amet, consectetur ng elit, sed do eiusmod tempor incididunt ut labore et dolore magna aliqua.</p>
  </div>
  <div class="card" style="left:781px">
    <svg width="70" height="70" viewBox="0 0 70 70" fill="none" stroke="#1fc6ee" stroke-width="2"><rect x="10" y="30" width="50" height="34" rx="3"/><path d="M29 42 L23 47 L29 52 M41 42 L47 47 L41 52"/><rect x="22" y="6" width="26" height="18" rx="2"/></svg>
    <h3>Business Analyst</h3>
    <p>Lorem ipsum dolor sit amet, consectetur ng elit, sed do eiusmod tempor incididunt ut labore et dolore magna aliqua.</p>
  </div>
</section>

<section class="how">
  <div class="photo" role="img" aria-label="Photo of developers working together at computers in a brick-walled office"></div>
  <h2><b>How can you build</b><br>software with us?</h2>
  <ul>
    <li>Brainstorm for a product that will solve a problem</li>
    <li>Plan the entire process</li>
    <li>Incorporate ideas from business partners or stakeholders</li>
    <li>Design the product</li>
    <li>Outsource the development team</li>
    <li>Develop the product</li>
    <li>Deploy the product</li>
    <li>Sell the product to the target market</li>
  </ul>
  <p class="note">Connect with us, and together, let's transform your visions and goals into reality.</p>
</section>

<section class="case">
  <h2 class="h2"><b>Case</b> study</h2>
  <p>Many business owners have great ideas but no experience with the actual product. Once you have an idea in mind, you will require software development aid at some point – whether your concept is for next-generation software or an inventive approach to offering an existing service. It might also be the development of a mobile app or web-based software. Whatever product you're working on, you'll need a technical co-founder to help you get it off the ground.</p>
  <div class="outline">FIND OUT MORE</div>
  <div class="video" role="img" aria-label="Video still of a team meeting in a bright office">
    <div class="play"><svg width="14" height="16"><path d="M2 1 L13 8 L2 15 Z" fill="#13a3e8"/></svg></div>
  </div>
</section>

<section class="contact">
  <h2 class="h2"><b>Get in</b> touch</h2>
  <p class="lead">Lorem ipsum dolor sit amet, consectetur adipcing elit, sed do eiusmod tempor incididunt ut labore et dolore magna aliqua.</p>
  <hr>
  <div class="info" style="top:342px"><span class="ic"><svg width="16" height="20" viewBox="0 0 16 20"><path d="M8 0 C3.6 0 0 3.4 0 7.6 C0 13 8 20 8 20 C8 20 16 13 16 7.6 C16 3.4 12.4 0 8 0Z" fill="#13a3e8"/><circle cx="8" cy="7.5" r="3" fill="#fff"/></svg></span>123 Your Adress Goes Here.<br>CA, 1234567</div>
  <div class="info" style="top:414px"><span class="ic"><svg width="20" height="20" viewBox="0 0 20 20"><path d="M4 1 L8 5 L6 8 C7 11 9 13 12 14 L15 12 L19 16 L16 19 C8 19 1 12 1 4 Z" fill="none" stroke="#13a3e8" stroke-width="1.8"/></svg></span>+1 888 888 8888</div>
  <div class="info" style="top:485px"><span class="ic"><svg width="20" height="14" viewBox="0 0 20 14"><rect x="1" y="1" width="18" height="12" fill="none" stroke="#13a3e8" stroke-width="1.8"/><path d="M1 1 L10 8 L19 1" fill="none" stroke="#13a3e8" stroke-width="1.8"/></svg></span>info@pellowar.com</div>

  <div class="lbl" style="left:650px;top:104px">Full Name:</div>
  <div class="field" style="left:650px;top:130px;width:440px;height:54px"></div>
  <div class="lbl" style="left:650px;top:226px">Email:</div>
  <div class="field" style="left:650px;top:252px;width:208px;height:54px"></div>
  <div class="lbl" style="left:881px;top:226px">Phone No:</div>
  <div class="field" style="left:881px;top:252px;width:209px;height:54px"></div>
  <div class="lbl" style="left:650px;top:347px">Messages:</div>
  <div class="field" style="left:650px;top:373px;width:440px;height:120px"></div>
  <div class="btn" style="left:651px;top:521px;width:165px;height:49px">Submit Now</div>
</section>

<footer class="footer">
  <div class="flogo"><div class="mark"></div><span>PELLOWAR</span></div>
  <div class="fcol" style="left:424px"><h4>Quick Links</h4><a>Home</a><a>About Us</a><a>Services</a><a>Team</a><a>Case Study</a><a>Contact</a></div>
  <div class="fcol" style="left:616px"><h4>Customer Service</h4><a>Privacy Policy</a><a>Terms of Conditions</a><a>Sitemap</a><a>FAQ's</a></div>
  <div class="fcol" style="left:855px"><h4>Stat Conected</h4><div class="social"><i></i><i></i><i></i><i></i></div><p>Lorem ipsum dolor st amet, consectetur adipiscing elit, sed do</p></div>
  <hr>
  <div class="copy">Copyright © 2022 &nbsp;PELLOWAR All Rights Reserved.</div>
</footer>

</body>
</html>
```